Stationery Design Project for Nimbora, Chicago

Nimbora, a street parking application which helps car drivers find a street parking spot by offering an ideal path along which to look for parking. This path is calculated by our algorithm based on data (e.g. historical data, baseball games schedule, etc.). Along this path the driver will find a spot and will also save 70% of the search time. Customer we target is reg. between 21 and 45 yo.

We envision something young, fresh, bright and original. Slightly abstract maybe. It should represent the idea and elements of finding street parking in the city, e.g. car(s), parking spot, people, city, etc. (just ideas!).

Logo is attached.

Requirement:
- Business Cards (2 Sided Full Color CMYK)
- Letterhead (1 Sided Full Color CMYK)
- Envelope (1 Sided Full Color CMYK)
- Sticker (1 Sided Full Color CMYK), round with a 2inch diameter.

Reason: We're starting to get more and more designs and need more time to look into all of them. Very exciting!! Thanks to everybody!

Hi all, we're in the process of selecting our favs. Though choices!!! Really good submissions. Will keep you posted and sorry for the delay.

Target Market(s)

Car drivers and owners between 21 and 45

Industry/Entity Type

Parking

Requirements
Must have
• Sticker should be round and include company URL nimbora.com and the new logo which we will attach soon.
Should not have
• Should not be too serious or boring.

```html
<!DOCTYPE html>
<html lang="en">
<head>
<meta charset="utf-8">
<title>Nimbora Business Card</title>
<link rel="stylesheet" href="https://fonts.googleapis.com/css2?family=Open+Sans:wght@400;600;700&display=swap">
<style>
  :root {
    --page: #e9e6e2;
    --white: #ffffff;
    --blue-deep: #1f5aa8;
    --blue-mid: #2f7fc8;
    --blue-light: #3aa3e0;
    --ink: #2b2b2b;
    --ink-soft: #4a4a4a;
    --photo-a: #8e9297;
    --photo-b: #c9ccd0;
  }
  html, body {
    margin: 0;
    width: 1200px;
    height: 758px;
    overflow: hidden;
    background: var(--page);
    font-family: "Open Sans", Arial, sans-serif;
  }
  .stage {
    position: relative;
    width: 1200px;
    height: 758px;
  }
  .card {
    position: absolute;
    top: 219px;
    width: 560px;
    height: 320px;
    border-radius: 18px;
    overflow: hidden;
    box-shadow: 0 6px 18px rgba(0,0,0,0.25);
  }
  /* Front */
  .card-front {
    left: 27px;
    background: var(--white);
  }
  .front-brand {
    position: absolute;
    top: 30px;
    left: 0;
    width: 100%;
    display: flex;
    justify-content: center;
    align-items: center;
    gap: 16px;
  }
  .brand-dot {
    width: 62px;
    height: 62px;
    border-radius: 50%;
    background: var(--blue-mid);
  }
  .brand-name {
    font-size: 54px;
    font-weight: 600;
    color: var(--ink);
    letter-spacing: 0.5px;
    line-height: 1;
  }
  .front-band {
    position: absolute;
    top: 140px;
    left: 0;
    width: 100%;
    height: 120px;
    background: linear-gradient(180deg, var(--blue-mid) 0%, var(--blue-deep) 100%);
  }
  .front-band::before {
    content: "";
    position: absolute;
    top: 0;
    left: 0;
    width: 100%;
    height: 44px;
    background: var(--blue-light);
    opacity: 0.55;
  }
  .person {
    position: absolute;
    top: 52px;
    right: 300px;
    text-align: right;
    color: var(--white);
  }
  .person-name {
    font-size: 22px;
    font-weight: 700;
    line-height: 1.1;
  }
  .person-title {
    font-size: 16px;
    line-height: 1.3;
  }
  .divider {
    position: absolute;
    top: 18px;
    left: 272px;
    width: 1px;
    height: 86px;
    background: rgba(255,255,255,0.7);
  }
  .contacts {
    position: absolute;
    top: 14px;
    left: 286px;
    margin: 0;
    padding: 0;
    list-style: none;
    color: var(--white);
    font-size: 13px;
    line-height: 21px;
  }
  .contacts li {
    display: flex;
    align-items: center;
    gap: 7px;
  }
  .contacts svg {
    width: 11px;
    height: 11px;
    fill: var(--white);
  }
  .address {
    position: absolute;
    bottom: 22px;
    left: 0;
    width: 100%;
    text-align: center;
    font-size: 13px;
    color: var(--ink-soft);
  }
  /* Back */
  .card-back {
    left: 613px;
    background: linear-gradient(180deg, var(--blue-deep) 0%, var(--blue-mid) 55%, var(--blue-light) 100%);
  }
  .back-brand {
    position: absolute;
    top: 98px;
    left: 40px;
    display: flex;
    align-items: center;
    gap: 14px;
  }
  .back-brand .brand-dot {
    width: 78px;
    height: 78px;
    background: var(--white);
    opacity: 0.9;
  }
  .back-brand .brand-name {
    font-size: 34px;
    color: var(--white);
  }
  .street-photo {
    position: absolute;
    top: 60px;
    right: 22px;
    width: 262px;
    height: 190px;
    border-radius: 6px;
    background: linear-gradient(135deg, var(--photo-a) 0%, var(--photo-b) 100%);
    box-shadow: 0 0 16px 8px rgba(58,163,224,0.6) inset;
  }
</style>
</head>
<body>
<main class="stage">
  <section class="card card-front" aria-label="Business card front">
    <div class="front-brand">
      <span class="brand-dot"></span>
      <span class="brand-name">nimbora</span>
    </div>
    <div class="front-band">
      <div class="person">
        <div class="person-name">Your Name</div>
        <div class="person-title">Title</div>
      </div>
      <span class="divider"></span>
      <ul class="contacts">
        <li><svg viewBox="0 0 12 12"><path d="M2 1h2.5l1 3-1.5 1a7 7 0 0 0 3 3l1-1.5 3 1V11a1 1 0 0 1-1 1A10 10 0 0 1 1 2a1 1 0 0 1 1-1z"/></svg>123-456-789</li>
        <li><svg viewBox="0 0 12 12"><rect x="3" y="0" width="6" height="12" rx="1"/></svg>123-456-789</li>
        <li><svg viewBox="0 0 12 12"><path d="M0 2h12v8H0z M0 2l6 5 6-5" stroke="#1f5aa8" stroke-width="1"/></svg>info@nimbora.com</li>
        <li><svg viewBox="0 0 12 12"><circle cx="6" cy="6" r="6"/></svg>www.nimbora.com</li>
      </ul>
    </div>
    <div class="address">Complex name, Street name, City, State, zip code</div>
  </section>

  <section class="card card-back" aria-label="Business card back">
    <div class="back-brand">
      <span class="brand-dot"></span>
      <span class="brand-name">nimbora</span>
    </div>
    <div class="street-photo" role="img" aria-label="Photo of cars parked in marked street parking bays seen from above"></div>
  </section>
</main>
</body>
</html>
```